Business card for law firm

Need business card for new law firm. Think confident, authoritative, conservative, but not stuffy or old-fashioned.

Contact Information for Business Card

Content for card - logo (uploaded), plus the following:

Paul Whitcombe (larger font)
Managing Partner (larger font, but not as large as name)
Level 9, 7 Ferris Lane
Sydney NSW 2000
Main Tel 02 9364 2710
Direct Tel 02 8472 3159
Email paul@qvlegal.com.au
www.qvlegal.com.au

Letterhead design should include logo plus:
Level 9, 7 Ferris Lane
Sydney NSW 2000
Tel 02 8472 3159
www.qvlegal.com.au

```html
<!DOCTYPE html>
<html lang="en">
<head>
<meta charset="utf-8">
<title>Quayvale Lawyers – Business Card</title>
<link rel="stylesheet" href="https://fonts.googleapis.com/css2?family=Cinzel:wght@500&family=Open+Sans:wght@400;600&display=swap">
<style>
  :root {
    --backdrop: #8d8d8d;
    --card: #ffffff;
    --navy: #0c1f5c;
    --ink: #0a0a0a;
    --text: #222222;
    --rule: #b5b5b5;
    --white: #ffffff;
  }
  * { margin: 0; padding: 0; box-sizing: border-box; }
  html, body { width: 1200px; height: 1200px; overflow: hidden; }
  body { background: var(--backdrop); position: relative; font-family: "Open Sans", Arial, sans-serif; }

  .card {
    position: absolute;
    top: 310px;
    width: 366px;
    height: 594px;
    background: var(--card);
  }
  .card--front { left: 233px; text-align: center; color: var(--text); }
  .card--back { left: 627px; width: 370px; }

  .brand-square {
    position: absolute;
    left: 166px; top: 96px;
    width: 34px; height: 34px;
    background: var(--navy);
  }
  .brand-name {
    position: absolute;
    left: 0; right: 0; top: 198px;
    font-family: "Cinzel", Georgia, serif;
    font-weight: 500;
    color: var(--ink);
    line-height: 1;
  }
  .brand-name__firm { display: block; font-size: 44px; letter-spacing: 1px; }
  .brand-name__kind { display: block; font-size: 16px; letter-spacing: 12px; margin-top: 10px; padding-left: 12px; }

  .person { position: absolute; left: 0; right: 0; top: 328px; }
  .person__name {
    font-family: "Cinzel", Georgia, serif;
    font-weight: 500;
    font-size: 23px;
    color: var(--navy);
    line-height: 1.1;
  }
  .person__role { font-size: 17px; line-height: 1.2; margin-top: 1px; }

  .icon-row {
    position: absolute; left: 93px; top: 384px;
    width: 180px; height: 20px;
    display: flex; align-items: center; justify-content: center; gap: 3px;
  }
  .icon-row::before, .icon-row::after {
    content: ""; flex: 1; height: 1px; background: var(--rule); margin: 0 5px;
  }
  .icon { width: 20px; height: 18px; background: var(--navy); display: block; }

  .contact { position: absolute; left: 0; right: 0; top: 412px; font-size: 16.5px; line-height: 21.3px; }
  .contact small { font-size: 14px; }
  .contact-rule { position: absolute; left: 93px; width: 180px; top: 507px; height: 1px; background: var(--rule); }
  .address { position: absolute; left: 0; right: 0; top: 515px; font-size: 16.5px; line-height: 21px; }

  .back-field {
    position: absolute; inset: 0;
    background: linear-gradient(180deg, var(--navy) 0%, #0a1640 55%, var(--ink) 100%);
  }
  .back-url {
    position: absolute; left: 0; right: 0; top: 523px;
    text-align: center; color: var(--white);
    font-weight: 600; font-size: 16.5px; letter-spacing: 0.2px;
  }
</style>
</head>
<body>

<section class="card card--front">
  <div class="brand-square"></div>
  <div class="brand-name">
    <span class="brand-name__firm">QUAYVALE</span>
    <span class="brand-name__kind">LAWYERS</span>
  </div>

  <div class="person">
    <div class="person__name">PAUL WHITCOMBE</div>
    <div class="person__role">Managing Partner</div>
  </div>

  <div class="icon-row">
    <svg class="icon" viewBox="0 0 20 18" aria-hidden="true"><path d="M5 6c0-2 10-2 10 0v1h-3V6H8v1H5z M6 8h8l1 6H5z" fill="#fff"/></svg>
    <svg class="icon" viewBox="0 0 20 18" aria-hidden="true"><path d="M5 6c0-2 10-2 10 0v1h-3V6H8v1H5z M6 8h8l1 6H5z" fill="#fff"/><circle cx="10" cy="11" r="1.6" fill="#0c1f5c"/></svg>
    <svg class="icon" viewBox="0 0 20 18" aria-hidden="true"><rect x="4" y="5" width="12" height="8" fill="none" stroke="#fff" stroke-width="1.3"/><path d="M4 5l6 5 6-5" fill="none" stroke="#fff" stroke-width="1.3"/></svg>
    <svg class="icon" viewBox="0 0 20 18" aria-hidden="true"><circle cx="10" cy="9" r="5" fill="#fff"/><path d="M7 7h3v2H8z M11 10h2v3h-2z" fill="#0c1f5c"/></svg>
  </div>

  <div class="contact">
    <div>02 9364 2710</div>
    <div>02 8472 3159 <small>(DIRECT)</small></div>
    <div>paul@qvlegal.com.au</div>
    <div>www.qvlegal.com.au</div>
  </div>
  <div class="contact-rule"></div>
  <div class="address">
    <div>Level 9, 7 Ferris Lane</div>
    <div>Sydney NSW 2000</div>
  </div>
</section>

<section class="card card--back">
  <div class="back-field" role="img" aria-label="Large brand symbol in navy and black on white"></div>
  <div class="back-url">www.qvlegal.com.au</div>
</section>

</body>
</html>
```